Business Cards + Flyer + Letterhead for Care Recruitment Agency

We are a recruitment agency for the health & care sector. We need designs made for business cards, A5 double-sided flyer, and a letterhead template.

Our branding message is professionalism, care, compassion, expertise. We are experts in recruitment for the care & health industry.

Our logo source files and colours are here - https://www.filevault-example.net/sh/q8rn27lpzw4xkc/BBRtLm3QPW92dKfYhNvZceLmo?dl=0

For the business card, I have attached an example we like. We want a vertical business card design, something very similar to the example given. The design should match our logo in terms of brand colors. On one side should be our logo, our website (www.holbrookelune.co.uk) and Care Recruitment Specialists written somewhere visible that fits, between our logo and the website at the bottom. On the other side should be our details.

Details on the front:

Logo with slogan
Care Recruitment Specialists
www.holbrookelune.co.uk

Details on the back:

Dominic Argyros
Managing Director

Radley Court, 40-48 Pellow St, Birmingham, B7 9QX
07612 495137
dominic@holbrookelune.co.uk
www.holbrookelune.co.uk

Nadia Holbrooke
Business Development Director

07731 284956
nadia@holbrookelune.co.uk
www.holbrookelune.co.uk

For the A5 flyer, I have attached some pictures we've used for the website, which could be used for the flyer as well. To get a better idea of our branding, please visit our website - https://holbrookelune.co.uk/

The text for the flyer is also attached.

Finally, the letterhead template should be a docx template with our logo and our identifiable branding (the same shapes and matching colours you will come up with for the business cards and flyer).

```html
<!DOCTYPE html>
<html lang="en">
<head>
<meta charset="utf-8">
<title>Holbrooke Lune Letterhead</title>
<link rel="stylesheet" href="https://fonts.googleapis.com/css2?family=Montserrat:wght@300;700&family=Lato:wght@400&family=Roboto+Condensed:wght@300;400&display=swap">
<style>
  :root {
    --navy: #1f2d5c;
    --sky: #3ec8f2;
    --brand-blue: #2f6fc0;
    --ink: #565656;
    --paper: #ffffff;
    --backdrop: #d8d8d8;
  }
  * { margin: 0; padding: 0; box-sizing: border-box; }
  html, body { width: 1056px; height: 1200px; overflow: hidden; }
  body { background: var(--backdrop); position: relative; }

  .letterhead {
    position: absolute; left: 104px; top: 0;
    width: 848px; height: 1200px;
    background: var(--paper);
    color: var(--ink);
  }

  .brand {
    position: absolute; left: 80px; top: 104px;
    display: flex; align-items: center; gap: 12px;
  }
  .brand-mark {
    width: 34px; height: 34px; border-radius: 50%;
    background: var(--brand-blue); flex: none;
  }
  .brand-name {
    font-family: "Roboto Condensed", sans-serif; font-weight: 400;
    font-size: 28px; color: var(--navy); white-space: nowrap;
  }

  .contact {
    position: absolute; left: 620px; top: 80px;
    font-family: "Lato", sans-serif; font-style: normal;
    font-size: 12.5px; color: var(--navy); line-height: 15px;
  }
  .contact-address { margin-bottom: 8px; }
  .contact-row { display: flex; align-items: center; gap: 7px; height: 18px; }
  .contact-row svg { width: 11px; height: 11px; flex: none; }

  .letter-date {
    position: absolute; left: 80px; top: 360px;
    font-family: "Montserrat", sans-serif; font-weight: 300; font-size: 19px;
  }
  .recipient-name {
    position: absolute; left: 80px; top: 393px;
    font-family: "Montserrat", sans-serif; font-weight: 700; font-size: 30px;
    letter-spacing: 0.3px;
  }
  .recipient-title {
    position: absolute; left: 80px; top: 436px;
    font-family: "Montserrat", sans-serif; font-weight: 300; font-size: 18px;
  }

  .letter-body {
    position: absolute; left: 80px; top: 510px; width: 688px;
    font-family: "Roboto Condensed", sans-serif; font-weight: 300;
    font-size: 16.2px; line-height: 29.3px; text-align: justify;
  }
  .letter-body p + p { margin-top: 29.5px; }

  .sign-off {
    position: absolute; left: 80px; top: 962px;
    font-family: "Roboto Condensed", sans-serif; font-weight: 300; font-size: 17px;
  }
  .signature {
    position: absolute; left: 81px; top: 1008px;
    width: 88px; height: 62px;
    background: var(--navy); opacity: 0.14; border-radius: 4px;
  }

  .footer-band { position: absolute; left: 0; bottom: 0; width: 848px; height: 21px; }
</style>
</head>
<body>
  <main class="letterhead">
    <header>
      <div class="brand">
        <div class="brand-mark"></div>
        <div class="brand-name">Holbrooke Lune</div>
      </div>

      <address class="contact">
        <div class="contact-address">Radley Court, 40-48<br>Pellow St, Birmingham, B7 9QX</div>
        <div class="contact-row">
          <svg viewBox="0 0 24 24" aria-hidden="true"><path fill="var(--brand-blue)" d="M6.6 10.8a15.2 15.2 0 0 0 6.6 6.6l2.2-2.2a1 1 0 0 1 1-.25 11.4 11.4 0 0 0 3.6.57 1 1 0 0 1 1 1V20a1 1 0 0 1-1 1A17 17 0 0 1 3 4a1 1 0 0 1 1-1h3.5a1 1 0 0 1 1 1c0 1.25.2 2.45.57 3.57a1 1 0 0 1-.25 1z"/></svg>
          <span>07612 495137</span>
        </div>
        <div class="contact-row">
          <svg viewBox="0 0 24 24" aria-hidden="true"><rect x="2" y="5" width="20" height="14" rx="1" fill="var(--brand-blue)"/><path d="M2.5 5.5 12 13l9.5-7.5" fill="none" stroke="#fff" stroke-width="1.6"/></svg>
          <span>dominic@holbrookelune.co.uk</span>
        </div>
        <div class="contact-row">
          <svg viewBox="0 0 24 24" aria-hidden="true"><g fill="none" stroke="var(--brand-blue)" stroke-width="1.6"><circle cx="12" cy="12" r="9.5"/><ellipse cx="12" cy="12" rx="4" ry="9.5"/><path d="M2.5 12h19M4 7h16M4 17h16"/></g></svg>
          <span>www.holbrookelune.co.uk</span>
        </div>
      </address>
    </header>

    <section class="recipient">
      <div class="letter-date">10 December, 2020</div>
      <div class="recipient-name">MICHAEL SMITH</div>
      <div class="recipient-title">Cheif Executive Officer</div>
    </section>

    <section class="letter-body">
      <p>Contrary to popular belief, Lorem Ipsum is not simply random text. It has roots in a piece of classical Latin literature from 45 BC, making it over 2000 years old. Richard Ashcombe, a Latin professor at Marlowe-Fenwick College in Virginia, looked up one of the more obscure Latin words, consectetur.</p>
      <p>Lorem Ipsum comes from sections 1.10.32 and 1.10.33 of "de Finibus Bonorum et Malorum" (The Extremes of Good and Evil) by Varenius, written in 45 BC. This book is a treatise on the theory of ethics, very popular during the Renaissance. The first line of Lorem Ipsum.</p>
      <p>The standard chunk of Lorem Ipsum used since the 1500s is reproduced below for those interested. Sections 1.10.32 and 1.10.33 from "de Finibus Bonorum et Malorum" by Varenius are also reproduced in their exact original.</p>
      <p>The standard chunk of Lorem Ipsum used since the 1500s is reproduced below for those interested.</p>
    </section>

    <div class="sign-off">Best Regards</div>
    <div class="signature" role="img" aria-label="Handwritten signature of the sender"></div>

    <svg class="footer-band" viewBox="0 0 848 21" preserveAspectRatio="none" aria-hidden="true">
      <polygon points="0,0 616,0 595,21 0,21" fill="var(--navy)"/>
      <polygon points="627,0 848,0 848,21 606,21" fill="var(--sky)"/>
    </svg>
  </main>
</body>
</html>
```